Brookvane Consulting Business Card Design

Business Card Design for Brookvane Consulting. Brookvane Consulting is a boutique consultancy based in Atlanta, GA., that specializes in marketing strategy, organization planning, and leadership development. We provide solutions for small businesses and startups as well as Vantage 300 companies.

http://brookvaneconsulting.com/

Target Market(s)

We provide solutions for small businesses and startups as well as Vantage 300 companies.

Industry/Entity Type

Consulting

Contact Information for Business Card

Two sided business card with priority on contact information, logo, tag line (Clarity to Plan Boldly, Act Wisely, Grow Further)

Colors

Designer to choose colors to be used in the design.

Requirements
Must have
• contact information, logo, tag line (Clarity to Plan Boldly, Act Wisely, Grow Further)
• Simple no over communication.
Nice to have
• I would like to see different placements of logo and creative use of both sides of the card
Should not have
• Do not put too much information on the card.

```html
<!DOCTYPE html>
<html lang="en">
<head>
<meta charset="utf-8">
<title>Brookvane Consulting Business Card</title>
<link href="https://fonts.googleapis.com/css2?family=Roboto:wght@400;500&family=Roboto+Condensed:wght@500&display=swap" rel="stylesheet">
<style>
  :root {
    --page-bg: #e9e6e1;
    --card-dark: #1c1c1d;
    --card-back: #222223;
    --ink-white: #f4f4f4;
    --ink-grey: #a9a9a9;
    --ink-dark: #1c1c1d;
    --rule: #e6e6e6;
  }
  * { margin: 0; padding: 0; box-sizing: border-box; }
  html, body { width: 1200px; height: 960px; overflow: hidden; }
  body {
    background: var(--page-bg);
    font-family: "Roboto", Arial, sans-serif;
    position: relative;
  }
  .card {
    position: absolute;
    width: 600px;
    height: 343px;
    box-shadow: 0 3px 8px rgba(0,0,0,.35);
  }
  .card-front { left: 314px; top: 113px; background: var(--card-dark); }
  .card-back { left: 312px; top: 472px; background: var(--card-back); }

  .brand-name {
    color: var(--ink-white);
    font-weight: 500;
    font-size: 34px;
    letter-spacing: .5px;
    white-space: nowrap;
  }
  .card-front .brand-name { position: absolute; left: 31px; top: 60px; }

  .contact { position: absolute; left: 31px; top: 172px; }
  .person-name {
    font-family: "Roboto Condensed", Arial, sans-serif;
    font-weight: 500;
    font-size: 20px;
    color: var(--ink-grey);
    letter-spacing: .3px;
  }
  .person-title { color: var(--ink-white); font-size: 15px; font-weight: 500; margin-top: 3px; }
  .contact-list { list-style: none; margin-top: 12px; }
  .contact-list li {
    color: var(--ink-white);
    font-size: 14px;
    display: flex;
    align-items: center;
    gap: 8px;
    height: 20px;
  }
  .contact-list svg { width: 13px; height: 13px; fill: var(--ink-grey); }

  .web-rule {
    position: absolute; left: 0; right: 0; top: 297px;
    height: 2px; background: var(--rule);
  }
  .web-address {
    position: absolute; left: 322px; top: 284px;
    width: 243px; height: 27px;
    background: #fff;
    color: var(--ink-dark);
    font-size: 14px; font-weight: 500;
    letter-spacing: .4px;
    display: flex; align-items: center; justify-content: center;
  }

  .back-texture { position: absolute; inset: 0; background: var(--card-back); }
  .card-back .brand-name {
    position: absolute; left: 0; right: 0; top: 140px;
    text-align: center; font-size: 40px;
  }
  .tagline {
    position: absolute; left: 0; right: 0; top: 281px;
    text-align: center;
    color: var(--ink-white);
    font-size: 14px;
  }
</style>
</head>
<body>
  <section class="card card-front">
    <div class="brand-name">Brookvane Consulting</div>
    <div class="contact">
      <div class="person-name">DARIUS WHITFIELD</div>
      <div class="person-title">Founder/Managing Director</div>
      <ul class="contact-list">
        <li>
          <svg viewBox="0 0 24 24" aria-hidden="true"><path d="M6.6 10.8a15.1 15.1 0 0 0 6.6 6.6l2.2-2.2c.3-.3.7-.4 1-.2 1.1.4 2.3.6 3.6.6.6 0 1 .4 1 1V20c0 .6-.4 1-1 1A17 17 0 0 1 3 4c0-.6.4-1 1-1h3.5c.6 0 1 .4 1 1 0 1.3.2 2.5.6 3.6.1.3 0 .7-.2 1z"/></svg>
          404-555-0172
        </li>
        <li>
          <svg viewBox="0 0 24 24" aria-hidden="true"><path d="M2 5h20v14H2z M3.5 6.5 12 12.5l8.5-6z" fill-rule="evenodd"/></svg>
          darius@brookvaneconsulting.com
        </li>
      </ul>
    </div>
    <div class="web-rule"></div>
    <div class="web-address">www.brookvaneconsulting.com</div>
  </section>

  <section class="card card-back">
    <div class="back-texture" role="img" aria-label="Subtle dark grid pattern across the card back"></div>
    <div class="brand-name">Brookvane Consulting</div>
    <p class="tagline">Clarity to Plan Boldly, Act Wisely, Grow Further</p>
  </section>
</body>
</html>
```